Moxy Fen needs some awesome stationary

Do you have what it takes to get my brand? You either do or you don't, have a crack at a design and you my just win my business.

I don't want to waste your or my time, so put your creative genius on either a business card or envelope.

I however need a package of stationary that follows the same brand. I will message you to complete the remaining should I like your first submission.

Here is what I need, have a go!

Basically I need the following for my small business based in melbourne.
- Letterhead (printer ready and MS Word)
- Business Card
- Compliments Slip
- Envelope
- Proposal Cover Page (MS Word only)
- Presentation Folder
- Marbled Fox Cards
- Student Name Tent
- Index Cards
- Vell-Ka

I am establishing the brand and it must be modern, professional but also relaxed; that is not formal and not corporate. It represents a company are leaders, but small enough to care and operate like a bunch of friends. We are bringing people and conversations back to business, and turfing out all the bureaucracy and crazy and wasteful procedures. Its about "lets talk and figure it out together and find even better ways".

Target Market(s)

Mainly companies that build software products, but Agile practices are used in many other industries (even graphic design projects)

Industry/Entity Type

Information Technology

Font styles to use
Sans Serif

Colors
3176b5
aaaaaa

Requirements
Must have
• I like curves and circles and not boxes or rectangles.
• I want a colour rich design with my brand colours, but it must be balanced.
• I want more modern than traditional, but simple modern
Should not have
• Not corporate
• Please don't waste my time if your not going to think about it.
• Don't mess with my primary logo
• Don't change my colours
• Don't overlay logo on image

```html
<!DOCTYPE html>
<html lang="en">
<head>
<meta charset="utf-8">
<title>Moxy Fen Letterhead</title>
<link rel="stylesheet" href="https://fonts.googleapis.com/css2?family=Arimo:wght@400;700&family=Open+Sans:wght@400;600;700&display=swap">
<style>
  :root {
    --brand-blue: #3176b5;
    --brand-blue-deep: #1f5fa3;
    --brand-grey: #aaaaaa;
    --grey-light: #d9d9d9;
    --faint: #eef0f6;
    --ink: #2a2a2a;
    --paper: #ffffff;
    --backdrop: #b9c4dd;
  }
  * { box-sizing: border-box; margin: 0; padding: 0; }
  html, body { width: 1200px; height: 784px; overflow: hidden; }
  body {
    background: var(--backdrop);
    font-family: "Arimo", Arial, sans-serif;
    color: var(--ink);
    position: relative;
  }
  .letterhead {
    position: absolute;
    left: 335px; top: 18px;
    width: 530px; height: 748px;
    background: var(--paper);
    box-shadow: 0 6px 22px rgba(40, 60, 110, 0.25);
    overflow: hidden;
  }
  /* header */
  .header-rule {
    position: absolute; left: 0; top: 42px;
    width: 392px; height: 4px;
    background: var(--brand-blue);
  }
  .header-rule::after {
    content: ""; position: absolute; left: 0; top: 6px;
    width: 392px; height: 1px; background: var(--brand-blue);
  }
  .company {
    position: absolute; left: 16px; top: 12px;
    font-family: "Open Sans", sans-serif;
    color: var(--brand-blue-deep);
  }
  .company-name { font-size: 11px; font-weight: 700; line-height: 14px; }
  .company-abn { font-size: 7px; color: var(--brand-blue); line-height: 10px; }
  .brand-mark {
    position: absolute; right: 26px; top: 20px;
    display: flex; align-items: center; gap: 8px;
    font-family: "Open Sans", sans-serif;
    font-weight: 700; font-size: 19px;
    color: var(--brand-blue);
  }
  .brand-dot {
    width: 30px; height: 30px; border-radius: 50%;
    background: var(--brand-blue);
  }
  .edge-tab {
    position: absolute; right: 0; top: 76px;
    width: 6px; height: 60px;
    background: linear-gradient(90deg, var(--grey-light), var(--brand-grey));
  }
  /* body */
  .letter-body {
    position: absolute; left: 96px; top: 100px; width: 342px;
    font-size: 8.6px; line-height: 12.4px;
  }
  .letter-body p { margin-bottom: 11px; }
  .signature {
    position: absolute; left: 230px; top: 470px;
    width: 120px; height: 38px;
    background: linear-gradient(90deg, #f3f3f3, #e6e6e6);
    border-radius: 4px;
  }
  /* footer */
  .footer-decor {
    position: absolute; left: -40px; bottom: 86px;
    width: 150px; height: 150px; border-radius: 50%;
    background: var(--faint);
  }
  .footer-contacts {
    position: absolute; left: 18px; right: 18px; bottom: 22px;
    display: flex; justify-content: space-between; align-items: center;
    font-family: "Open Sans", sans-serif;
    font-size: 7.4px; color: #666;
  }
  .contact { display: flex; align-items: center; gap: 5px; }
  .contact svg { width: 10px; height: 10px; fill: var(--brand-blue); flex: none; }
  .footer-rule {
    position: absolute; left: 0; right: 0; bottom: 8px; height: 4px;
    background: linear-gradient(90deg, var(--brand-grey) 0 14%, var(--brand-blue) 14% 100%);
  }
</style>
</head>
<body>
  <main class="letterhead">
    <header>
      <div class="company">
        <div class="company-name">Moxy Fen Pty Ltd</div>
        <div class="company-abn">ABN 52 614 803 927</div>
      </div>
      <div class="header-rule"></div>
      <div class="brand-mark"><span class="brand-dot"></span><span>Moxy Fen</span></div>
      <div class="edge-tab"></div>
    </header>

    <section class="letter-body">
      <p>Lorem Ipsum is simply dummy text of the printing and typesetting industry. Lorem Ipsum has been the industry's standard dummy text ever since the 1500s, when an unknown printer took a galley of type and scrambled it to make a type specimen book. It has survived not only five centuries, but also the leap into electronic typesetting, remaining essentially unchanged. It was popularised in the 1960s with the release of Dryline sheets containing Lorem Ipsum passages, and more recently with desktop publishing software like Quillset Layout including versions of Lorem Ipsum.</p>
      <p>It is a long established fact that a reader will be distracted by the readable content of a page when looking at its layout. The point of using Lorem Ipsum is that it has a more-or-less normal distribution of letters, as opposed to using 'Content here, content here', making it look like readable English. Many desktop publishing packages and web page editors now use Lorem Ipsum as their default model text, and a search for 'lorem ipsum' will uncover many web sites still in their infancy. Various versions have evolved over the years, sometimes by accident, sometimes on purpose (injected humour and the like).</p>
      <p>Contrary to popular belief, Lorem Ipsum is not simply random text. It has roots in a piece of classical Latin literature from 45 BC, making it over 2000 years old. Tobias Wrenfield, a Latin professor at Ashgrove College, looked up one of the more obscure Latin words, consectetur, from a Lorem Ipsum passage, and going through the cites of the word in classical literature, discovered the undoubtable source. Lorem Ipsum comes from sections 1.10.32 and 1.10.33 of an old text on the extremes of good and evil. The generated Lorem Ipsum is therefore always free from repetition, injected humour, or non-characteristic words etc.</p>
    </section>
    <div class="signature" role="img" aria-label="Handwritten signature of the sender"></div>

    <footer>
      <div class="footer-decor"></div>
      <div class="footer-contacts">
        <span class="contact">
          <svg viewBox="0 0 10 10"><path d="M5 0a3.5 3.5 0 0 0-3.5 3.5C1.5 6 5 10 5 10s3.5-4 3.5-6.5A3.5 3.5 0 0 0 5 0zm0 5a1.4 1.4 0 1 1 0-2.8A1.4 1.4 0 0 1 5 5z"/></svg>
          PO Box 4417, Larkin Vale, VIC 3190, Australia
        </span>
        <span class="contact">
          <svg viewBox="0 0 10 10"><path d="M2.2 0.5l1.6 2.3-1 1c.6 1.4 1.6 2.4 3 3l1-1 2.3 1.6-.9 1.9C4.6 9.2.8 5.4.3 1.4z"/></svg>
          1300 669 336
        </span>
        <span class="contact">
          <svg viewBox="0 0 10 10"><path d="M0 2h10v6H0zM.8 2.6L5 5.6l4.2-3z" fill-rule="evenodd"/></svg>
          hello@moxyfen.com.au
        </span>
        <span class="contact">
          <svg viewBox="0 0 10 10"><circle cx="5" cy="5" r="4.6"/></svg>
          www.moxyfen.com.au
        </span>
      </div>
      <div class="footer-rule"></div>
    </footer>
  </main>
</body>
</html>
```